Website Homepage re-design Project

I run a large format poster printing business & have a website hosted on vantrelstore using one of their templates, http://www.brimlowprints.co.uk
I am looking to update the home page to give it a more professional look, it must be clear for our clients to choose their poster type from the homepage
The design must contain the 5 poster type categories as well as most of the information above the poster categories, most of the text below the green "terms & conditions" footer can be left as it is as it's used for keywords, maybe just tidied up a bit
I would like to keep the customer reviews & sample posters on the home page along with the quick glance (fly-out) poster prices
I would also like the 4 step ordering process graphic updated, ie where it say "Select Poster Type" "Choose Poster Size" etc, there are 4 variations of this graphic which I will need to insert in their respective pages
If something can be done with the company name "Brimlow Prints & Sealers" that would be great.
I would prefer a design which shows all the information down to the section where it says "Order Your Poster Here" displayed on the screen when the page is loaded

```html
<!DOCTYPE html>
<html lang="en">
<head>
<meta charset="utf-8">
<title>Brimlow Prints &amp; Sealers — Home</title>
<link rel="stylesheet" href="https://fonts.googleapis.com/css2?family=Exo:wght@400;500;600&family=Mulish:wght@400;600;700&display=swap">
<style>
:root{
  --teal:#12728f;
  --teal-dark:#0a4256;
  --teal-deep:#073444;
  --link:#1a7fb0;
  --ink:#222;
  --text:#555;
  --muted:#666;
  --rule:#cfcfcf;
  --hero-top:#f4f4f4;
  --hero-bottom:#e2e2e2;
  --steps:#262626;
  --steps-low:#1a1a1a;
  --step-active:#2a9fd6;
  --footer:#0f6c8b;
}
*{box-sizing:border-box;margin:0;padding:0}
html,body{width:1051px;height:1200px;overflow:hidden}
body{position:relative;background:#fff;font-family:"Mulish",sans-serif;color:var(--text)}
.hero-bg{position:absolute;left:0;top:0;width:1051px;height:581px;background:linear-gradient(#f6f6f6,var(--hero-bottom));border-bottom:2px solid #222}
.lower-band{position:absolute;left:0;top:925px;width:1051px;height:220px;background:#f1f1f1}

.brand{position:absolute;left:26px;top:24px;display:flex;align-items:center;gap:12px;font-family:"Exo",sans-serif;font-weight:500;font-size:34px;color:var(--teal);letter-spacing:.3px}
.brand-mark{width:46px;height:46px;background:var(--teal)}

.cart{position:absolute;right:22px;top:11px;font-size:13px;color:var(--ink)}
.cart a{color:var(--link);text-decoration:none}
.lang{position:absolute;left:951px;top:42px;width:79px;height:25px;background:#ddd;border:1px solid #ccc;font-size:13px;color:#777;padding:4px 0 0 8px}
.lang-flag{position:absolute;left:38px;top:5px;width:24px;height:14px;background:#2a3d7a}
.lang-caret{position:absolute;right:6px;top:10px;border:4px solid transparent;border-top-color:#444}
.search{position:absolute;left:836px;top:77px;width:193px;height:25px;background:#d4d4d4;font-size:13px;color:#fff;padding:4px 0 0 12px}
.search-btn{position:absolute;right:0;top:0;width:26px;height:25px;background:var(--teal-dark)}

.nav{position:absolute;left:57px;top:114px;width:937px;height:36px;background:linear-gradient(var(--teal),var(--teal-deep));border-radius:3px}
.nav a{position:absolute;top:10px;transform:translateX(-50%);font-size:13px;color:#fff;text-decoration:none;letter-spacing:.3px;white-space:nowrap}
.nav .active{position:absolute;left:11px;top:2px;width:107px;height:34px;background:linear-gradient(#1c88a8,#0e5e78)}

.hero-title{position:absolute;left:58px;top:263px;width:440px;font-family:"Exo",sans-serif;font-weight:600;font-size:22px;line-height:24px;color:#2d2d2d;text-transform:uppercase}
.hero-text{position:absolute;left:58px;top:345px;width:430px;font-size:12.5px;line-height:19px;color:#444}
.hero-photo{position:absolute;left:568px;top:226px;width:397px;height:276px;background:linear-gradient(135deg,#2b2b2b 0 55%,#d84a78 55% 80%,#cfcfcf 80%);border-radius:6px}

.steps{position:absolute;left:37px;top:524px;width:978px;height:122px;background:linear-gradient(var(--steps),#202020);border-radius:5px;overflow:hidden}
.step{position:absolute;top:0;width:244px;height:122px;border-right:1px solid #3a3a3a}
.step-name{position:absolute;left:27px;top:14px;font-family:"Exo",sans-serif;font-size:22px;color:#fff}
.step-sub{position:absolute;left:27px;top:42px;font-family:"Exo",sans-serif;font-size:15px;color:#999}
.step-icon{position:absolute;left:134px;top:10px;width:70px;height:68px;border-radius:6px}
.step-num{position:absolute;left:0;top:82px;width:244px;height:40px;background:var(--steps-low);border-top:1px solid #333;font-family:"Exo",sans-serif;font-size:19px;color:#bbb;padding:8px 0 0 50px}
.step-num.current{color:var(--step-active)}
.step-num::before{content:"";position:absolute;left:26px;top:-1px;border:9px solid transparent;border-top-color:#2a2a2a}

.categories{position:absolute;left:26px;top:688px;width:999px;height:280px;background:#fff;border:1px solid #ccc;box-shadow:0 3px 6px rgba(0,0,0,.15)}
.categories-head{height:38px;background:linear-gradient(#fafafa,#ececec);border-bottom:2px solid #444;font-size:21px;color:#333;padding:6px 0 0 19px}
.category{position:absolute;top:52px}
.category h2{font-size:18px;font-weight:600;line-height:21px;color:var(--ink)}
.category p{position:absolute;top:56px;width:100%;font-size:12.5px;line-height:19px;color:var(--muted)}
.category-rule{position:absolute;top:58px;width:1px;height:196px;background:var(--rule)}

.testimonials-title,.contact-title{position:absolute;top:980px;font-size:18px;font-weight:600;color:var(--ink)}
.review{position:absolute;top:1013px;width:305px;font-size:12.5px;line-height:19px;color:#444}
.review strong{display:block;font-size:11.5px;color:#333}
.divider{position:absolute;left:703px;top:988px;width:1px;height:142px;background:#bbb}
.address{position:absolute;left:733px;top:1016px;font-size:12px;line-height:19px;color:#333}
.phones{position:absolute;left:901px;top:1016px;font-size:12px;line-height:19px;color:#333}
.social{position:absolute;left:901px;top:1103px;display:flex;gap:6px}
.social span{width:17px;height:17px;background:var(--teal)}

.footer{position:absolute;left:0;top:1145px;width:1051px;height:55px;background:var(--footer);color:#fff;font-size:12.5px;text-align:center;padding-top:18px}
</style>
</head>
<body>
<div class="hero-bg"></div>
<div class="lower-band"></div>

<div class="brand"><span class="brand-mark"></span>Brimlow Prints &amp; Sealers</div>

<div class="cart">My cart : <a href="#">(0) items</a> | <a href="#">Check out</a></div>
<div class="lang">Eng<span class="lang-flag"></span><span class="lang-caret"></span></div>
<div class="search">Search<span class="search-btn">
  <svg width="26" height="25" viewBox="0 0 26 25"><circle cx="12" cy="11" r="5" fill="none" stroke="#fff" stroke-width="2"/><line x1="16" y1="15" x2="20" y2="19" stroke="#fff" stroke-width="2"/></svg>
</span></div>

<nav class="nav">
  <span class="active"></span>
  <a href="#" style="left:64px">HOME</a>
  <a href="#" style="left:186px">ABOUT US</a>
  <a href="#" style="left:328px">CONTACT US</a>
  <a href="#" style="left:452px">FAQ</a>
  <a href="#" style="left:605px">COLOUR CALIBRATION</a>
  <a href="#" style="left:818px">CUSTOMER COMMENTS</a>
</nav>

<h1 class="hero-title">Large format full colour photographic &amp; presentation quality posters</h1>
<p class="hero-text">Poster printing at 2400dpi on the highest Quality 190gsm Photo Papers using the latest Vantix V6100 Photo Printers with 8 COLOUR PIGMENT Inks* producing Millions of vibrant colours that will not fade over time</p>
<div class="hero-photo" role="img" aria-label="Large format photo printer printing a colourful poster"></div>

<section class="steps">
  <div class="step" style="left:0">
    <div class="step-name">Poster</div><div class="step-sub">Type</div>
    <div class="step-icon" role="img" aria-label="Poster sample icon" style="background:linear-gradient(#f2a33a,#3a2a10)"></div>
    <div class="step-num current">Step 1</div>
  </div>
  <div class="step" style="left:244px">
    <div class="step-name">Choose</div><div class="step-sub">Poster size</div>
    <div class="step-icon" role="img" aria-label="Drawing tools icon" style="background:linear-gradient(#d8d8d8,#b79a4a)"></div>
    <div class="step-num">Step 2</div>
  </div>
  <div class="step" style="left:488px">
    <div class="step-name">Upload</div><div class="step-sub">your File</div>
    <div class="step-icon" role="img" aria-label="Globe with upload arrow icon" style="background:radial-gradient(circle,#3aa3d8,#0d4f7a);border-radius:50%"></div>
    <div class="step-num">Step 3</div>
  </div>
  <div class="step" style="left:732px;border-right:0">
    <div class="step-name">Checkout</div><div class="step-sub">Pay for posters</div>
    <div class="step-icon" role="img" aria-label="Stack of banknotes icon" style="left:148px;background:linear-gradient(#cfd8c0,#7a8a60)"></div>
    <div class="step-num">Step 4</div>
  </div>
</section>

<section class="categories">
  <div class="categories-head">Poster categories</div>
  <div class="category" style="left:15px;width:170px"><h2>Matt Photo Paper</h2><p>Photo Quality Poster printing, Printed at 2400 dpi on 180gsm Silk Matt Photo paper, perfect for high quality presentations &amp; matt photo reproduction, these poster will show the finest details</p></div>
  <div class="category-rule" style="left:198px"></div>
  <div class="category" style="left:215px;width:170px"><h2>Gloss Photo Paper</h2><p>Photo Quality Poster Printing, Printed at 2400 dpi on 190gsm Gloss Photo paper, perfect for high quality presentations &amp; photographic prints with vivid true to life colours.</p></div>
  <div class="category-rule" style="left:397px"></div>
  <div class="category" style="left:410px;width:190px"><h2>Student Presentation Poster</h2><p style="width:170px">Photo Quality Poster Printing, Printed at 1200dpi on 170gsm High Resolution coated paper, this printing option is ideally suited to students presentations</p></div>
  <div class="category-rule" style="left:606px"></div>
  <div class="category" style="left:619px;width:172px"><h2>Poster with Gloss Encapsulating</h2><p>Photo Quality Poster printing &amp; Laminating. Printed at 2400 dpi &amp; Laminated on both sides with a 5mm edge seal, the Gloss finish enhances the colours. Weatherproof &amp; durable, these posters are ideal for long term use</p></div>
  <div class="category-rule" style="left:801px"></div>
  <div class="category" style="left:815px;width:170px"><h2>Poster with Matt Encapsulating</h2><p>Photo Quality Poster printing &amp; Laminating. Printed at 2400dpi &amp; Laminated on both sides with a 5mm edge seal, the Matt finish reduces light reflection. Weatherproof &amp; durable, these posters are ideal for long term use</p></div>
</section>

<h2 class="testimonials-title" style="left:33px">Testimonials</h2>
<div class="review" style="left:38px"><strong>Reviewer: Elin</strong>Hi Gareth, I have just gotten my prints. They look amazing! I am stunned by the quality! I look forward to using your service again in the next university year. Thank you so much! Elin</div>
<div class="review" style="left:374px"><strong>Reviewer: Elin</strong>Hi Gareth, I have just gotten my prints. They look amazing! I am stunned by the quality! I look forward to using your service again in the next university year. Thank you so much! Elin</div>

<div class="divider"></div>
<h2 class="contact-title" style="left:732px">Contact us</h2>
<address class="address" style="font-style:normal">Brimlow Prints &amp; Sealers<br>Nant Uchaf<br>Heol Brynmawr<br>Cefnderwen<br>Llanarth<br>SA47 9TR</address>
<div class="phones">tel: 01632 960417<br>mob: 07700 900 582<br><br>fax: 01632 960893</div>
<div class="social" aria-label="Social links"><span></span><span></span><span></span><span></span><span></span></div>

<footer class="footer">2012 © copyright.brimlowprints&amp;sealers.received</footer>
</body>
</html>
```